Bramblewood Card Company Business Cards

We are a trading card store with Glimmorax, sports and other TCG cards, we need a business card design that encompasses a clean cut, modern style with a retro flare. website is bramblewoodcardco.com for reference. Can utilize a comic book era feel or a more modern outdoor feel to utilize the "Pacific Northwest" elements of tress, mountains, etc.

Industry/Entity Type

Trading cards and collectibles

Contact Information for Business Card

business name, email address, phone number, name, owner job title

Font styles to use
Sans Serif

```html
<!DOCTYPE html>
<html lang="en">
<head>
<meta charset="utf-8">
<title>Bramblewood Card Company – Business Cards</title>
<link href="https://fonts.googleapis.com/css2?family=Montserrat:wght@400;500;700;800&display=swap" rel="stylesheet">
<style>
  :root {
    --brand-cyan: #22bfe0;
    --brand-grey: #6d6e70;
    --ink: #3a3a3c;
    --card-white: #ffffff;
    --stage-top: #cfcfcf;
    --stage-bottom: #9e9e9e;
  }
  * { box-sizing: border-box; margin: 0; padding: 0; }
  html, body { width: 1200px; height: 815px; overflow: hidden; }
  body {
    background: linear-gradient(180deg, var(--stage-top), var(--stage-bottom));
    font-family: "Montserrat", sans-serif;
    display: flex;
    align-items: center;
    justify-content: center;
    gap: 40px;
  }
  .card {
    width: 540px;
    height: 309px;
    border-radius: 22px;
    box-shadow: 0 14px 30px rgba(0,0,0,0.25);
    position: relative;
    overflow: hidden;
  }
  .card--front { background: var(--card-white); }
  .card--back {
    background: var(--brand-cyan);
    display: flex;
    align-items: center;
    justify-content: center;
  }
  .brand-mark {
    display: flex;
    align-items: center;
    gap: 10px;
    font-weight: 800;
    text-transform: uppercase;
    letter-spacing: 1px;
    line-height: 1.15;
  }
  .brand-mark__square {
    width: 16px;
    height: 16px;
    flex: none;
  }
  .card--front .brand-mark {
    position: absolute;
    left: 34px;
    top: 50%;
    transform: translateY(-50%);
    width: 190px;
    color: var(--brand-grey);
    font-size: 19px;
  }
  .card--front .brand-mark__square { background: var(--brand-cyan); }
  .card--back .brand-mark {
    color: var(--brand-grey);
    font-size: 28px;
    width: 300px;
  }
  .card--back .brand-mark__square { background: var(--brand-grey); width: 22px; height: 22px; }
  .contact-block {
    position: absolute;
    left: 262px;
    top: 42px;
    right: 24px;
    color: var(--ink);
  }
  .contact-block__name {
    color: var(--brand-cyan);
    font-weight: 700;
    font-size: 25px;
    letter-spacing: 1px;
    text-transform: uppercase;
  }
  .contact-block__title { font-size: 13px; margin-top: 2px; }
  .contact-block__address { font-size: 13px; line-height: 1.45; margin-top: 8px; }
  .contact-block__rule {
    height: 1.5px;
    background: var(--brand-cyan);
    margin: 16px 0 14px;
  }
  .contact-list { list-style: none; font-size: 12.5px; line-height: 1.55; }
  .contact-list li { display: flex; align-items: center; gap: 8px; }
  .contact-list svg { width: 11px; height: 11px; flex: none; fill: var(--brand-cyan); }
</style>
</head>
<body>
  <section class="card card--front" aria-label="Business card front">
    <div class="brand-mark">
      <span class="brand-mark__square"></span>
      <span>Bramblewood Card Company</span>
    </div>
    <div class="contact-block">
      <h1 class="contact-block__name">Dorian Vale</h1>
      <p class="contact-block__title">Manager</p>
      <p class="contact-block__address">482 Cedar Ridge Lane 12<br>Alder Falls, WA 98214</p>
      <div class="contact-block__rule"></div>
      <ul class="contact-list">
        <li><svg viewBox="0 0 12 12"><path d="M2.5 1l2 2.2-1 1.3a6 6 0 0 0 3.9 3.9l1.3-1 2.2 2-1.2 1.5C5.5 10.7 1.3 6.5.9 2.2z"/></svg>(206)555-0148</li>
        <li><svg viewBox="0 0 12 12"><path d="M3 0h6a1 1 0 0 1 1 1v10a1 1 0 0 1-1 1H3a1 1 0 0 1-1-1V1a1 1 0 0 1 1-1zm0 1.5v8h6v-8z"/></svg>(206)555-01927</li>
        <li><svg viewBox="0 0 12 12"><path d="M0 2h12v8H0zm1 1v.4l5 3.3 5-3.3V3z"/></svg>hello@bramblewoodcardco.com</li>
        <li><svg viewBox="0 0 12 12"><path d="M6 0a6 6 0 1 0 0 12A6 6 0 0 0 6 0zm0 1.2c.7.8 1.2 2.2 1.3 4.2H4.7C4.8 3.4 5.3 2 6 1.2zM1.3 6.6h2.2c.1 1.6.4 2.9 1 3.9a4.8 4.8 0 0 1-3.2-3.9zm0-1.2a4.8 4.8 0 0 1 3.2-3.9c-.6 1-.9 2.3-1 3.9zm3.4 1.2h2.6c-.1 2-.6 3.4-1.3 4.2-.7-.8-1.2-2.2-1.3-4.2zm3.8 0h2.2a4.8 4.8 0 0 1-3.2 3.9c.6-1 .9-2.3 1-3.9zm0-1.2c-.1-1.6-.4-2.9-1-3.9a4.8 4.8 0 0 1 3.2 3.9z"/></svg>www.bramblewoodcardco.com</li>
      </ul>
    </div>
  </section>

  <section class="card card--back" aria-label="Business card back">
    <div class="brand-mark">
      <span class="brand-mark__square"></span>
      <span>Bramblewood Card Company</span>
    </div>
  </section>
</body>
</html>
```